Swiftcoinswap.com Mobile App

Swiftcoinswap.com is an online Beurea de change. They buy and sell currency from individuals and large corporations.

The app will compliment the main website of the company and focus on specific features as set out in our brief document. overall the design must be high-quality, easy navigate with a one finger operation and nice clean design.

This content is for the design of 3 screen

Loading screen
Homepage screen
Buy Currency for Branch Collection screen

attached is a full brief, but the loading screen will incorporate the logo and the home screen must allow easy navigation to 6 key button features that will enable you to go to each section of the app.

The winner will get to design the remaining screens of the app which are approx 15/18 further screens, based on the same layout.

If you can code the app as well into iPhone and Android, please make this known as well.
Updates

Hello,

For further inspritation for the Home screen, we quite like the interface on the uploaded image lumavo-home.jpg

So you slide left and right with your finger to the button, instead of a list format or something quite 2d. Almost 3d like interface maybe with an option to display all as a list?

See what sort of creativity can be achieved.

thanks

Target Market(s)

Consumers mainly aged between 25-60

Industry/Entity Type

It Company

Requirements
Must have
• good clean visually stunning appearance with apply shiny effect buttons and navigation

```html
<!DOCTYPE html>
<html lang="en">
<head>
<meta charset="utf-8">
<title>Swiftcoinswap – Exchange Rates</title>
<link href="https://fonts.googleapis.com/css2?family=Bebas+Neue&display=swap" rel="stylesheet">
<style>
  :root {
    --bg-top: #ffffff;
    --bg-bottom: #e2e2e2;
    --brand-blue: #1a5fa8;
    --bar-light: #4a4a4a;
    --bar-dark: #1c1c1c;
    --panel-light: #545454;
    --panel-dark: #2a2a2a;
    --field-dark: #2c2c2c;
    --field-light: #3c3c3c;
    --text-light: #f2f2f2;
    --chip-blue: #1f6ec0;
    --chip-blue-dark: #0e4585;
    --chip-red: #e0202a;
    --chip-red-dark: #a3141b;
  }
  * { box-sizing: border-box; margin: 0; padding: 0; }
  html, body { width: 800px; height: 1200px; overflow: hidden; }
  body {
    position: relative;
    font-family: "Bebas Neue", "Arial Narrow", sans-serif;
    background: radial-gradient(ellipse 90% 60% at 50% 28%, var(--bg-top) 0%, #f3f3f3 55%, var(--bg-bottom) 100%);
  }
  .brand {
    position: absolute; left: 52px; top: 50px;
    display: flex; align-items: center; gap: 14px;
    color: var(--brand-blue); font-size: 56px; letter-spacing: 1px; line-height: 1;
  }
  .brand-dot { width: 26px; height: 26px; border-radius: 50%; background: var(--brand-blue); }

  .nav-bar {
    position: absolute; left: 0; top: 154px; width: 800px; height: 81px;
    background: linear-gradient(var(--bar-light), #2e2e2e 50%, var(--bar-dark));
    border-top: 1px solid #666; box-shadow: 0 3px 6px rgba(0,0,0,.35);
  }
  .nav-chip {
    position: absolute; top: 162px; width: 66px; height: 66px; border-radius: 50%;
    background: radial-gradient(circle at 50% 30%, #3d8ee0, var(--chip-blue) 45%, var(--chip-blue-dark));
    border: 3px solid #151515; box-shadow: inset 0 2px 2px rgba(255,255,255,.35);
    display: flex; align-items: center; justify-content: center;
  }
  .nav-tab {
    position: absolute; left: 200px; top: 148px; width: 403px; height: 92px;
    background: linear-gradient(#4e4e4e, #262626 50%, #141414);
    border-radius: 5px; border: 1px solid #0b0b0b;
    box-shadow: 0 4px 8px rgba(0,0,0,.45), inset 0 1px 0 rgba(255,255,255,.25);
  }
  .nav-tab .chip-active {
    position: absolute; left: 13px; top: 13px; width: 66px; height: 66px; border-radius: 50%;
    background: radial-gradient(circle at 50% 30%, #ff5a60, var(--chip-red) 45%, var(--chip-red-dark));
    border: 3px solid #111; display: flex; align-items: center; justify-content: center;
  }
  .nav-tab h1 {
    position: absolute; left: 105px; top: 20px;
    color: var(--text-light); font-weight: 400; font-size: 52px; letter-spacing: 1px; line-height: 1;
  }

  .converter { position: absolute; left: 73px; top: 306px; width: 637px; }
  .rate-row, .action-btn {
    height: 77px; border-radius: 5px;
    background: linear-gradient(var(--panel-light), #393939 50%, var(--panel-dark));
    border: 1px solid #1a1a1a;
    box-shadow: 0 2px 3px rgba(0,0,0,.35), inset 0 1px 0 rgba(255,255,255,.2);
    color: var(--text-light); margin-bottom: 14px;
  }
  .rate-row { display: flex; padding: 6px; gap: 6px; }
  .amount {
    flex: 0 0 434px; border-radius: 3px; padding-left: 13px;
    background: linear-gradient(var(--field-dark), var(--field-light));
    box-shadow: inset 0 2px 4px rgba(0,0,0,.6); border: 1px solid #1a1a1a;
    font-size: 36px; line-height: 64px;
  }
  .currency {
    flex: 1; display: flex; align-items: center; justify-content: flex-end; gap: 26px; padding-right: 14px;
    border-left: 1px solid #222; font-size: 36px;
  }
  .action-btn {
    display: flex; align-items: center; justify-content: center;
    font-size: 36px; letter-spacing: .5px; text-shadow: 0 1px 2px rgba(0,0,0,.6);
  }
</style>
</head>
<body>
  <div class="brand"><span class="brand-dot"></span><span>Swiftcoinswap</span></div>

  <nav class="nav-bar"></nav>
  <div class="nav-chip" style="left:38px" aria-label="Currency flags">
    <svg width="30" height="30" viewBox="0 0 30 30" fill="none" stroke="#0a2f5c" stroke-width="2.5"><path d="M6 27V4M6 5h17l-4 6 4 6H6"/></svg>
  </div>
  <div class="nav-chip" style="left:122px" aria-label="Buy currency">
    <svg width="32" height="32" viewBox="0 0 32 32" fill="none" stroke="#0a2f5c" stroke-width="2.3"><ellipse cx="13" cy="8" rx="8" ry="3"/><path d="M5 8v12c0 2 4 3 8 3M21 8v5"/><path d="M5 14c0 2 4 3 8 3"/><circle cx="22" cy="22" r="6"/><path d="M22 19v6M19 22h6"/></svg>
  </div>
  <div class="nav-chip" style="left:626px" aria-label="Currency flags">
    <svg width="30" height="30" viewBox="0 0 30 30" fill="none" stroke="#0a2f5c" stroke-width="2.5"><path d="M6 27V4M6 5h17l-4 6 4 6H6"/></svg>
  </div>
  <div class="nav-chip" style="left:710px" aria-label="Currency flags">
    <svg width="30" height="30" viewBox="0 0 30 30" fill="none" stroke="#0a2f5c" stroke-width="2.5"><path d="M6 27V4M6 5h17l-4 6 4 6H6"/></svg>
  </div>

  <div class="nav-tab">
    <div class="chip-active">
      <svg width="36" height="36" viewBox="0 0 36 36" fill="none" stroke="#fff" stroke-width="4" stroke-linecap="round" stroke-linejoin="round"><path d="M7 15a11 8 0 0 1 20-3"/><path d="M28 6v7h-7"/><path d="M29 21a11 8 0 0 1-20 3"/><path d="M8 30v-7h7"/></svg>
    </div>
    <h1>Exchange Rates</h1>
  </div>

  <main class="converter">
    <div class="rate-row">
      <div class="amount">1.00</div>
      <div class="currency">GBP
        <svg width="16" height="10" viewBox="0 0 16 10" fill="none" stroke="#eee" stroke-width="3"><path d="M2 2l6 6 6-6"/></svg>
      </div>
    </div>
    <div class="rate-row">
      <div class="amount">1.154624</div>
      <div class="currency">EURO
        <svg width="16" height="10" viewBox="0 0 16 10" fill="none" stroke="#eee" stroke-width="3"><path d="M2 2l6 6 6-6"/></svg>
      </div>
    </div>
    <div class="action-btn">Buy Currency</div>
    <div class="action-btn">About This Rate</div>
  </main>
</body>
</html>
```